Flat bootstrap design for existing site

I'm looking for a modern flat design based around an existing logo. This has to be a custom design (no external templates), and implemented into a bootstrap framework.

The logo is attached as 2 versions - choose whichever you want, that flows better with whatever design you choose.

Added screenshots of the existing site (currently using the default bootstrap layouts). Please make your designs around those pages in the screenshots (i.e. the homepage only has the postal code input and the header). The active page has 3 screenshots, because I wanted to illustrate the other states that would be visible (in the table rows).

This is a moving/junk removal website, just for some context.

Here's some example websites (flat designs) that I like, just to give you an idea of what I'm after.

https://www.plimvora.com/
https://dacklow.com/
https://trevanu.com/
https://quobrintal.com/en/

Coding

Coded - Design and coding required

Number of Pages Required

5+ page

Colors

Designer to choose colors to be used in the design.

Requirements
Must have
• It must be a modern/simple flat design, that is built around the existing logo (attached).
• It has to be implemented using bootstrap.

```html
<!DOCTYPE html>
<html lang="en">
<head>
<meta charset="utf-8">
<title>Haulvo – Booking Details</title>
<link href="https://fonts.googleapis.com/css2?family=Montserrat:wght@400;500;600;700&display=swap" rel="stylesheet">
<style>
:root{
  --sky:#4bc8f4;
  --sky-btn:#4cc6f2;
  --ink:#111;
  --muted:#666;
  --label:#777;
  --panel:#fafafa;
  --white:#fff;
  --line:#e6e6e6;
  --green:#0fcc66;
  --blue:#0db4f2;
  --teal:#06607a;
  --pay:#0479aa;
  --avatar:#8a8f93;
}
*{box-sizing:border-box;margin:0;padding:0}
html,body{width:1200px;height:1178px;overflow:hidden}
body{font-family:"Montserrat",sans-serif;color:var(--ink);background:var(--white);position:relative}
.site-header{position:absolute;left:0;top:0;width:1200px;height:85px;background:var(--white)}
.brand{position:absolute;left:90px;top:24px;display:flex;align-items:center;gap:8px;color:var(--sky);font-weight:700;font-size:30px;letter-spacing:1px}
.brand-dot{width:18px;height:18px;border-radius:50%;background:var(--sky)}
.main-nav{position:absolute;left:467px;top:34px;display:flex;gap:43px;font-size:13px;font-weight:600}
.cta-driver{position:absolute;left:689px;top:21px;width:179px;height:43px;border-radius:22px;background:var(--sky-btn);color:var(--white);font-size:13px;font-weight:600;display:flex;align-items:center;justify-content:center}
.user-chip{position:absolute;left:880px;top:21px;width:170px;height:44px;border:1px solid #eee;border-radius:22px;display:flex;align-items:center;gap:9px;padding-left:4px;font-size:11px;color:#333}
.avatar{border-radius:50%;background:linear-gradient(135deg,#b7a58a,#5d6a50);flex:none}
.user-chip .avatar{width:36px;height:36px}
.caret{color:#bbb;font-size:9px}
.band{position:absolute;left:0;top:85px;width:1200px;height:1021px;background:var(--sky)}
.card{position:absolute;left:90px;top:141px;width:1020px;height:941px;background:var(--panel)}
.card-head{height:62px;background:var(--white);padding:20px 32px;font-size:17px;font-weight:500;color:#555}
.field-label{position:absolute;font-size:11px;font-weight:600;color:var(--label)}
.field{position:absolute;background:var(--white);display:flex;align-items:center;gap:10px;padding-left:14px;font-size:12px;color:#333}
.icon{width:17px;height:17px;flex:none}
.btn-update{position:absolute;left:26px;top:357px;width:178px;height:42px;border-radius:21px;background:var(--sky-btn);color:var(--white);font-size:13px;font-weight:600;display:flex;align-items:center;justify-content:center}
.section-title{position:absolute;left:24px;top:464px;font-size:17px;font-weight:600}
.drivers{position:absolute;left:23px;top:511px;width:980px;border-collapse:collapse;background:var(--panel)}
.drivers th,.drivers td{border:1px solid var(--line);text-align:left}
.drivers th{height:55px;font-size:13px;font-weight:700;padding-left:19px}
.drivers td{height:73px;font-size:11px;color:#333;padding-left:22px}
.drivers td.name{padding-left:19px;width:181px}
.drivers td.dist{width:183px}
.drivers td.pickup{border-right:none}
.drivers td.status,.drivers td.action{border-left:none}
.drivers .last{border-left:none}
.drivers th.pickup{padding-left:33px;border-right:none}
.who{display:flex;align-items:center;gap:12px;font-size:13px;color:#444}
.who .avatar{width:44px;height:44px}
.pill{display:inline-flex;align-items:center;justify-content:center;width:115px;height:29px;border-radius:15px;color:var(--white);font-size:11px;font-weight:700}
.pill.accepted{background:var(--green)}
.pill.sent{background:var(--blue)}
.pill.pending{background:var(--teal)}
.btn-pay{display:inline-flex;align-items:center;justify-content:center;width:119px;height:29px;background:var(--pay);color:var(--white);font-size:11px;font-weight:600}
.btn-more{position:absolute;left:433px;top:878px;width:154px;height:39px;border:3px solid #b8ecfb;border-radius:20px;display:flex;align-items:center;justify-content:center;font-size:11px;font-weight:600;color:#555;background:var(--white)}
.site-footer{position:absolute;left:0;top:1106px;width:1200px;height:72px;display:flex;align-items:center;justify-content:center;font-size:13px;color:#666}
</style>
</head>
<body>
<header class="site-header">
  <div class="brand"><span class="brand-dot"></span>HAULVO</div>
  <nav class="main-nav"><span>BOOK</span><span>HOW IT WORKS</span></nav>
  <div class="cta-driver">BECOME A DRIVER</div>
  <div class="user-chip"><span class="avatar" role="img" aria-label="User profile photo"></span>george@haulvo.in <span class="caret">▾</span></div>
</header>

<div class="band"></div>

<main class="card">
  <div class="card-head">Booking Details</div>

  <span class="field-label" style="left:18px;top:104px">Package Selected</span>
  <div class="field" style="left:18px;top:130px;width:477px;height:52px">
    <svg class="icon" viewBox="0 0 18 18"><rect x="1" y="4" width="16" height="12" rx="1" fill="#ddd"/><rect x="6" y="1.5" width="6" height="3" fill="none" stroke="#ddd" stroke-width="1.5"/></svg>Package 1
  </div>

  <span class="field-label" style="left:523px;top:104px">Pick-Up Time Selected</span>
  <div class="field" style="left:523px;top:130px;width:477px;height:52px">
    <svg class="icon" viewBox="0 0 18 18"><rect x="1.5" y="2.5" width="15" height="14" fill="none" stroke="#ccc"/><path d="M1.5 6h15M5 9h2M8 9h2M11 9h2M5 12h2M8 12h2M11 12h2" stroke="#ccc"/></svg>July 7th 2017 &nbsp;&nbsp;&nbsp;Time &nbsp;12:00 AM
  </div>

  <span class="field-label" style="left:18px;top:198px">Description</span>
  <div class="field" style="left:18px;top:221px;width:982px;height:104px;align-items:flex-start;padding:18px 20px">1 Large Stove</div>

  <div class="btn-update">UPDATE</div>

  <h2 class="section-title">Booking Details</h2>

  <table class="drivers">
    <tr><th>Name</th><th>Distance (Km)</th><th class="pickup" colspan="3">Agreed Pick Up Time</th></tr>
    <tr>
      <td class="name"><div class="who"><span class="avatar" role="img" aria-label="Driver photo"></span>Dale Brenner</div></td>
      <td class="dist">4.04 Km Away</td>
      <td class="pickup" style="padding-left:32px">July 18 at 4.13 am</td>
      <td class="status"><span class="pill accepted">Time Accepted</span></td>
      <td class="action last"><span class="btn-pay">Make Payment</span></td>
    </tr>
    <tr>
      <td class="name"><div class="who"><span class="avatar" role="img" aria-label="Driver photo"></span>Owen Tarrik</div></td>
      <td class="dist">4.04 Km Away</td>
      <td class="pickup" style="padding-left:34px">–</td>
      <td class="status"><span class="pill sent">Request Sent</span></td>
      <td class="action last"></td>
    </tr>
    <tr>
      <td class="name"><div class="who"><span class="avatar" role="img" aria-label="Driver photo"></span>Ravi Hollen</div></td>
      <td class="dist">4.04 Km Away</td>
      <td class="pickup" style="padding-left:34px">–</td>
      <td class="status"><span class="pill sent">Request Sent</span></td>
      <td class="action last"></td>
    </tr>
    <tr>
      <td class="name"><div class="who"><span class="avatar" role="img" aria-label="Driver photo"></span>Marco Dellin</div></td>
      <td class="dist">4.04 Km Away</td>
      <td class="pickup" style="padding-left:34px">–</td>
      <td class="status"><span class="pill pending">Pending</span></td>
      <td class="action last"></td>
    </tr>
  </table>

  <div class="btn-more">VIEW MORE DETAILS</div>
</main>

<footer class="site-footer">© 2017 Company Name &nbsp;| All Rights Reserved</footer>
</body>
</html>
```